Commit to H.E.A.L. (Healthy Eating and Living)Corporate Wellness

Pledge to T.R.I.M. (Tidy Motion In Routines) is my health and wellness company. I am a certified Health & Lifestyle Coach who provides a 6 month one-on-one coaching program for individuals and groups. I also provide 1 hour health seminars or "brown bag" lunches for any type of organization. My focus is on prevention of chronic disease through health and food education, as well as effective lifestyle coaching. I would like the brochure to have my logo, my name and certification, some health statistics, and my programs/seminars. Looking for a one page, half fold or trifold brochure design. I am flexible! I forgot to include my personal information. phone number 555/014-7739. email is marla@brightpathforwardnation.example. website is www.pledgetotrim.example.

Target Market(s)

Companies (large or small) looking for wellness and disease prevention programs for their employees.

Industry/Entity Type

Health

Requirements
Must have
• I am going into this with no picture in my head as to what I want. I like simplicity. I like to represent health, in all aspects, from food to environment. I will attach my logo to use, and colors should accent the logo.
I need it to include my name and title (Marla Vostrik, Certified Health & Lifestyle Coach). The tag line "Because your staff's vigor IS your bottom line." These statistics listed clearly: "1. The U.S. spends $2.8 trillion on health care every year, and this number is rising. 2. Treating individuals with chronic preventable disease is responsible for 75% of our health care costs. 3. The U.S. spends more on healthcare than Japan, Germany, France, China, UK, Italy, Canada, Brazil, Spain and Australia COMBINED. 4. The Global Vitality Council ranks the U.S. 37th for overall health outcomes. This means that more healthcare spending does not equate to better health.
Then it needs to say that "Our healthcare costs are out of control, increasing, and unsustainable. We do not have a healthcare system, we have a disease care system. Prevention of chronic disease is the only way to reduce our costs. Workplace wellness solutions MUST change behaviors. Food and health education, as well as effective lifestyle coaching are the keys to this behavior change."
I offer 1 hour seminars, sample seminars include but are not limited to "Cancer Prevention" "Nation's Plate/Nation's Ailment," and "Vigor & Balance starts where Ordinary Habits Stop." I also offer a six month bi-weekly health coaching program for individuals or small groups. Plus custom programs that include health food store tours, pantry purges, cooking ideas and preparation, etc.

```html
<!DOCTYPE html>
<html lang="en">
<head>
<meta charset="utf-8">
<title>Pledge to T.R.I.M. – Corporate Wellness</title>
<link rel="stylesheet" href="https://fonts.googleapis.com/css2?family=Philosopher&family=Tinos:wght@400;700&family=Arimo:wght@400;700&family=Raleway:wght@400;500&display=swap">
<style>
  :root {
    --paper: #ffffff;
    --green-deep: #0b4f24;
    --green-mid: #13823a;
    --green-bright: #2fa548;
    --lime: #9cc43a;
    --lime-pale: #dfe9a8;
    --lemon: #e8e79a;
    --ink-dark: #3b3b2e;
    --text-light: #ffffff;
    --frame-olive: #6c9a2c;
    --soft-white: #f1f1ee;
  }
  * { box-sizing: border-box; margin: 0; padding: 0; }
  html, body { width: 936px; height: 1200px; overflow: hidden; background: var(--paper); }
  .flyer { position: relative; width: 936px; height: 1200px; background: var(--paper); }
  .panel {
    position: absolute; left: 21px; top: 21px; width: 894px; height: 1160px; overflow: hidden;
    background:
      radial-gradient(ellipse 520px 420px at 280px 700px, var(--green-bright) 0%, rgba(47,165,72,0) 100%),
      linear-gradient(160deg, var(--green-mid) 20%, var(--green-deep) 70%, var(--green-mid) 100%);
  }
  .hero-photo {
    position: absolute; left: 0; top: 0; width: 894px; height: 430px;
    background:
      radial-gradient(circle 170px at 90px 80px, rgba(236,240,190,0.85), rgba(236,240,190,0) 100%),
      radial-gradient(ellipse 360px 220px at 600px 200px, var(--lemon), rgba(232,231,154,0) 100%),
      linear-gradient(180deg, var(--lime-pale) 0%, #b8cf72 45%, rgba(19,130,58,0) 100%);
  }
  .shapes { position: absolute; left: 0; top: 0; }
  .headline {
    position: absolute; right: 45px; top: 226px; text-align: right; font-weight: 400;
    font-family: 'Philosopher', sans-serif; color: var(--text-light); line-height: 1.15;
    text-shadow: 0 1px 3px rgba(0,0,0,0.25);
  }
  .headline .small { font-size: 29px; }
  .headline .big { font-size: 45px; }
  .manifesto {
    position: absolute; left: 52px; top: 361px; white-space: nowrap;
    font-family: 'Tinos', serif; font-size: 22px; line-height: 27px; color: var(--text-light);
  }
  .stats {
    position: absolute; left: 52px; top: 540px; white-space: nowrap;
    font-family: 'Tinos', serif; font-size: 16.5px; line-height: 19.5px; color: var(--text-light);
  }
  .stats p { margin-bottom: 14px; }
  .portrait {
    position: absolute; left: 52px; top: 783px; width: 210px; height: 196px;
    border: 6px solid var(--frame-olive);
    background: linear-gradient(180deg, #3d6a2e 0%, #6d8f4a 55%, #c9b79a 100%);
  }
  .coach { position: absolute; left: 53px; top: 1005px; font-family: 'Raleway', sans-serif; color: var(--text-light); }
  .coach .name { font-size: 19px; font-weight: 500; }
  .coach .title { font-size: 13px; margin-top: 2px; }
  .brand {
    position: absolute; left: 364px; top: 920px; width: 500px; text-align: center;
    font-family: 'Arimo', sans-serif;
  }
  .brand .mark { display: inline-flex; align-items: center; gap: 12px; font-size: 30px; color: var(--green-mid); }
  .brand .mark .dot { width: 22px; height: 22px; border-radius: 50%; background: var(--lime); display: inline-block; }
  .contact { position: absolute; left: 364px; top: 966px; width: 500px; text-align: center; font-family: 'Arimo', sans-serif; color: var(--ink-dark); }
  .contact .phone { font-size: 24px; font-weight: 700; line-height: 28px; }
  .contact .line { font-size: 19.5px; line-height: 24px; }
  .seminars {
    position: absolute; left: 0; top: 1065px; width: 894px; height: 95px; text-align: center;
    background: linear-gradient(90deg, #1d6a2a 0%, #4f9a30 35%, #1e6b2b 65%, #0c461d 100%);
    font-family: 'Arimo', sans-serif; color: var(--text-light); padding-top: 12px;
  }
  .seminars .lead { font-size: 17px; font-weight: 700; line-height: 23px; }
  .seminars .topic { font-size: 19px; line-height: 23px; }
</style>
</head>
<body>
<div class="flyer">
  <div class="panel">
    <div class="hero-photo" role="img" aria-label="Photo of fresh lemons and leaves in a basket"></div>

    <svg class="shapes" width="894" height="1160" viewBox="0 0 894 1160" aria-hidden="true">
      <defs>
        <linearGradient id="arc-band" x1="0" y1="1" x2="1" y2="0">
          <stop offset="0" stop-color="#5c8f22"/>
          <stop offset="0.5" stop-color="#a9cf3d"/>
          <stop offset="1" stop-color="#7fb236"/>
        </linearGradient>
      </defs>
      <path d="M259,1065 C290,800 570,640 894,630 L894,660 C580,672 310,830 284,1065 Z" fill="url(#arc-band)"/>
      <path d="M284,1065 C310,830 580,672 894,660 L894,1065 Z" fill="var(--soft-white)"/>
    </svg>

    <h1 class="headline">
      <span class="small">Because </span><span class="big">your staff's</span><span class="small"> vigor</span><br>
      <span class="small">IS </span><span class="big">your bottom line</span>
    </h1>

    <blockquote class="manifesto">“Our healthcare costs are out of control, increasing, and unsustainable.<br>We do not have a healthcare system, we have a disease care system.<br>Prevention of chronic disease is the only way to reduce our costs.<br>Workplace wellness solutions MUST change behaviors.<br>Food and health education, as well as effective lifestyle coaching are<br>the keys to this behavior change."</blockquote>

    <div class="stats">
      <p>The U.S. spends <b>$2.8 trillion</b> on health care every year,<br>and this number is rising.</p>
      <p>Treating individuals with chronic preventable disease<br>is responsible for <b>75%</b> of our health care costs.</p>
      <p>The U.S. spends more on <b>healthcare</b> than Japan,<br>Germany, France, China, UK, Italy, Canada, Brazil,<br>Spain and Australia COMBINED.</p>
      <p>The Global Vitality Council ranks<br>the U.S. <b>37th</b> for overall health outcomes.</p>
    </div>

    <div class="portrait" role="img" aria-label="Portrait photo of the health coach"></div>
    <div class="coach">
      <div class="name">Marla Vostrik</div>
      <div class="title">Certified Health &amp; Lifestyle Coach</div>
    </div>

    <div class="brand">
      <div class="mark"><span class="dot"></span>Pledge to T.R.I.M.</div>
    </div>

    <div class="contact">
      <div class="phone">555/014-7739</div>
      <div class="line">marla@brightpathforwardnation.example</div>
      <div class="line">www.pledgetotrim.example</div>
    </div>

    <div class="seminars">
      <div class="lead">JOIN TO 1 HOUR SEMINARS</div>
      <div class="topic">Cancer Prevention | Nation's Plate/Nation's Ailment</div>
      <div class="topic">Vigor &amp; Balance starts where Ordinary Habits Stop</div>
    </div>
  </div>
</div>
</body>
</html>
```